Business Card for Vorla Parts Wholesale supplier

Hi There! I need a new business card for our company. We are specialized in selling Vorla parts, mostly we sell new LCD screens for Zelnar and Drelks. I would like to see that back in the design.

You can find the colors and logo's on our website: www.hartuvo.nl

Industry/Entity Type

Business

Contact Information for Business Card

My Details:
Tobias Lindqvist

Phone: 0031687203316
E-mail: Tobias@hartuvo.nl

Slogan: "Because Quality Matters"

Font styles to use
Sans Serif

Colors

Designer to choose colors to be used in the design.

Requirements
Must have
• A Black backside with the Hartuvo logo on it. The front side should be clean with only my contact details.
• But I'm also open for something really different or awesome!
Nice to have
• Remember that we are in the parts & repairing industry, So i'll be handing those business cards mainly to repair companies. Maybe you can do something with that thought :)

```html
<!DOCTYPE html>
<html lang="en">
<head>
<meta charset="utf-8">
<title>Hartuvo Business Card</title>
<link href="https://fonts.googleapis.com/css2?family=Play:wght@400;700&display=swap" rel="stylesheet">
<style>
  :root {
    --backdrop: #b3b3b3;
    --card-white: #ffffff;
    --card-black: #1a1a1a;
    --brand-orange: #ee6a1f;
    --ink: #111111;
    --rule: #f0c7a8;
    --mark-grey: #b9b9b9;
  }
  * { margin: 0; padding: 0; box-sizing: border-box; }
  html, body {
    width: 1200px; height: 900px; overflow: hidden;
    background: var(--backdrop);
    font-family: "Play", "Arial", sans-serif;
  }
  .canvas { position: relative; width: 1200px; height: 900px; }
  .card {
    position: absolute; top: 271px;
    width: 457px; height: 282px;
    border-radius: 14px; overflow: hidden;
  }
  .card--front { left: 137px; background: var(--card-white); }
  .card--back { left: 626px; background: var(--card-black); width: 458px; }

  .wordmark {
    position: absolute; display: flex; align-items: center;
    font-weight: 700; line-height: 1; letter-spacing: 0.5px;
  }
  .wordmark__dot { border-radius: 50%; flex: none; }
  .card--front .wordmark { left: 27px; top: 27px; gap: 12px; color: var(--ink); font-size: 44px; }
  .card--front .wordmark__dot { width: 50px; height: 50px; background: var(--brand-orange); }
  .card--back .wordmark { left: 87px; top: 110px; gap: 14px; color: #ffffff; font-size: 58px; }
  .card--back .wordmark__dot { width: 62px; height: 62px; background: var(--mark-grey); }

  .tagline {
    position: absolute; left: 27px; top: 92px;
    font-size: 16px; color: var(--brand-orange);
  }
  .holder-name {
    position: absolute; left: 27px; top: 138px;
    font-size: 27px; font-weight: 700; color: var(--brand-orange);
  }
  .divider {
    position: absolute; left: 27px; top: 178px;
    width: 401px; height: 1px; background: var(--rule);
  }
  .contact-list {
    position: absolute; right: 28px; top: 190px;
    list-style: none;
  }
  .contact-list li {
    display: flex; justify-content: flex-end; align-items: center;
    gap: 9px; height: 21px;
    font-size: 13px; color: var(--ink);
  }
  .contact-list svg { width: 13px; height: 13px; flex: none; }

  .band { position: absolute; bottom: 0; height: 14px; }
  .band--orange { left: 0; width: 222px; background: var(--brand-orange); }
  .band--black { left: 235px; right: 0; background: #000000; }
</style>
</head>
<body>
<main class="canvas">
  <section class="card card--front" aria-label="Business card front">
    <div class="wordmark"><span class="wordmark__dot"></span><span>hartuvo</span></div>
    <p class="tagline">Because Quality Matters</p>
    <h1 class="holder-name">Tobias Lindqvist</h1>
    <div class="divider"></div>
    <ul class="contact-list">
      <li>0031687203316
        <svg viewBox="0 0 13 13" aria-hidden="true"><circle cx="6.5" cy="6.5" r="6.5" fill="var(--brand-orange)"/><path d="M3.5 5.5c0-1 1.3-1.6 3-1.6s3 .6 3 1.6l-1 .4-.5-.9h-3l-.5.9z M4.2 9.3l.8-2.6h3l.8 2.6z" fill="#fff"/></svg>
      </li>
      <li>Tobias@hartuvo.nl
        <svg viewBox="0 0 13 13" aria-hidden="true"><circle cx="6.5" cy="6.5" r="6.5" fill="var(--brand-orange)"/><rect x="3.5" y="4.3" width="6" height="4.4" fill="#fff"/><path d="M3.5 4.3l3 2.4 3-2.4" stroke="var(--brand-orange)" stroke-width="0.8" fill="none"/></svg>
      </li>
      <li>www.hartuvo.nl
        <svg viewBox="0 0 13 13" aria-hidden="true"><circle cx="6.5" cy="6.5" r="6.5" fill="var(--brand-orange)"/><circle cx="6.5" cy="6.5" r="3" fill="none" stroke="#fff" stroke-width="1.4"/></svg>
      </li>
    </ul>
    <div class="band band--orange"></div>
    <div class="band band--black"></div>
  </section>

  <section class="card card--back" aria-label="Business card back">
    <div class="wordmark"><span class="wordmark__dot"></span><span>hartuvo</span></div>
  </section>
</main>
</body>
</html>
```